One page flyer for nonprofit focused IT company

I need a one page flyer (one side of a single 8.5x11 page) with text and graphics. The company logo is already done, and it must appear on the flyer along with other icons and graphics. The final design will be printed on heavy weight glossy paper as a handout and also distributed as a PDF.

The text is provided in an attachment, if it needs to be shortened let me know.

Industry/Entity Type

Information Technology

Requirements
Must have
• some flare (colors, icons or images)
Should not have
• While we work for nonprofits, my company is a FOR PROFIT company.

```html
<!DOCTYPE html>
<html lang="en">
<head>
<meta charset="utf-8">
<title>Meridian Systems Corporation – Nonprofit IT Services Flyer</title>
<link rel="stylesheet" href="https://fonts.googleapis.com/css2?family=Arimo:ital,wght@0,400;0,700;1,700&family=Bebas+Neue&family=Roboto+Condensed:wght@400&display=swap">
<style>
  :root {
    --stage: #6f7a80;
    --header-red: #7a1f26;
    --header-deep: #4a1419;
    --glow-pink: #e0307a;
    --band-dark: rgba(38, 30, 32, 0.92);
    --ribbon-red: #9a1029;
    --ribbon-shadow: #3b0b14;
    --title-red: #9a1029;
    --body-text: #3a3a3a;
    --paper: #ffffff;
    --footer-red: #7b2024;
  }
  * { box-sizing: border-box; margin: 0; padding: 0; }
  html, body { width: 1200px; height: 1200px; overflow: hidden; }
  body { background: var(--stage); position: relative; font-family: "Arimo", Arial, sans-serif; }

  .flyer {
    position: absolute; left: 160px; top: 30px;
    width: 880px; height: 1139px;
    background: var(--paper);
    overflow: hidden;
  }

  .hero {
    position: absolute; left: 0; top: 0; width: 880px; height: 432px;
    background:
      radial-gradient(circle at 2% 58%, rgba(224, 48, 122, 0.75) 0, rgba(224, 48, 122, 0) 22%),
      radial-gradient(ellipse at 55% 10%, #a02a32 0, rgba(160, 42, 50, 0) 55%),
      linear-gradient(180deg, var(--header-red) 0%, var(--header-deep) 100%);
  }

  .logo-panel {
    position: absolute; left: 50px; top: 52px; width: 256px; height: 128px;
    background: var(--paper);
    display: flex; flex-direction: column; align-items: center; justify-content: center; gap: 12px;
  }
  .logo-square { width: 52px; height: 46px; background: var(--ribbon-red); }
  .logo-name {
    font-family: "Arimo", Arial, sans-serif; font-weight: 400; font-size: 16px;
    color: var(--ribbon-red); letter-spacing: 0.3px; text-align: center;
  }

  .intro-band {
    position: absolute; left: 0; top: 170px; width: 880px; height: 224px;
    background: linear-gradient(90deg, rgba(38,30,32,0) 0%, rgba(38,30,32,0.35) 30%, var(--band-dark) 44%);
  }

  .headline {
    position: absolute; left: 46px; top: 222px;
    font-family: "Bebas Neue", Impact, sans-serif; font-weight: 400; color: #fff; line-height: 1;
  }
  .headline-big { font-size: 82px; letter-spacing: 0.5px; }
  .headline-small { font-size: 48px; letter-spacing: 0; margin-top: 0; }

  .intro {
    position: absolute; left: 412px; top: 190px; width: 420px; color: #fff;
  }
  .intro h2 { font-size: 16.5px; font-weight: 700; line-height: 20px; margin-bottom: 6px; }
  .intro p { font-size: 15.2px; line-height: 19.8px; text-align: justify; }

  .successes-title {
    position: absolute; left: 153px; top: 440px;
    font-size: 23px; font-weight: 700; color: var(--title-red);
  }

  .ribbon {
    position: absolute; height: 30px;
    background: var(--ribbon-shadow);
    clip-path: polygon(0 0, calc(100% - 38px) 0, 100% 100%, 0 100%);
  }
  .ribbon span {
    display: flex; align-items: center; height: 27px; padding-left: 8px;
    width: calc(100% - 3px);
    background: var(--ribbon-red); color: #fff;
    font-size: 15.5px; font-weight: 700; white-space: nowrap;
    clip-path: polygon(0 0, calc(100% - 37px) 0, 100% 100%, 0 100%);
  }
  .ribbon.condensed span { font-family: "Roboto Condensed", "Arial Narrow", sans-serif; font-size: 15px; }

  .copy {
    position: absolute; color: var(--body-text);
    font-size: 15.2px; line-height: 19.8px; text-align: justify;
  }
  .copy.condensed { font-family: "Roboto Condensed", "Arial Narrow", sans-serif; font-size: 14.4px; }
  .copy.tight { font-size: 14.6px; letter-spacing: -0.15px; }
  .copy strong { font-weight: 700; }

  .solutions {
    position: absolute; left: 50px; top: 1054px;
    font-size: 15.5px; font-weight: 700; font-style: italic; line-height: 20px; color: #333;
  }

  .footer-band {
    position: absolute; left: 0; top: 1105px; width: 880px; height: 34px; background: var(--footer-red);
  }
</style>
</head>
<body>
<main class="flyer">
  <header class="hero" role="img" aria-label="Deep red header backdrop with a glowing pink network-of-dots pattern"></header>
  <div class="intro-band"></div>

  <div class="logo-panel">
    <div class="logo-square"></div>
    <div class="logo-name">Meridian Systems Corporation</div>
  </div>

  <h1 class="headline">
    <div class="headline-big">50 Years of</div>
    <div class="headline-small">Nonprofit IT Services</div>
  </h1>

  <section class="intro">
    <h2>Efficient and Elegant Approach to IT Solution Implementations</h2>
    <p>Meridian Systems Corporation has been supporting the Information Systems needs of nonprofits for over 50 years. We continually strive to bring the latest technologies and best practices to nonprofits to drive down the cost of IT while implementing systems that drive revenue. Our Agile approach to IT management means that we deliver working systems to every one of our clients every two weeks.</p>
  </section>

  <h2 class="successes-title">Successes</h2>

  <div class="ribbon" style="left:50px; top:475px; width:393px;"><span>90% Reduction in Software Development Costs</span></div>
  <p class="copy condensed" style="left:50px; top:513px; width:377px;">Harlow Research's National Auto Retailers Association needed to update their core product offering; they engaged their in-house IT department who estimated the project would take 3 years at a cost of $3,000,000. NARA decided to work with Meridian Systems Corporation instead, and the product was released to production in only 9 months at one tenth of the cost, only $300,000</p>

  <div class="ribbon" style="left:50px; top:642px; width:402px;"><span>10x Increase in Membership</span></div>
  <p class="copy tight" style="left:52px; top:674px; width:377px;">Greenway Paths Conservancy needed to move to online membership registration and contracted with Meridian Systems Corporation to build a significant online presence and engage potential members. Through compelling online tools and mobile applications Greenway Paths has <strong>increased membership 10 fold</strong>.</p>

  <div class="ribbon condensed" style="left:50px; top:806px; width:402px;"><span>20% Reduction in Overhead</span></div>
  <p class="copy condensed" style="left:51px; top:842px; width:376px;">The National Alliance for Civic Leaders had antiquated systems and processes in place to manage over 500 chapters across the nation. Working with MSC they implemented online tools to allow communication and management between the local chapters and national headquarters. This eliminated much of the overhead of chapter management, reducing HR costs by 20%.</p>
  <p class="copy" style="left:51px; top:961px; width:376px;">With a focus on non-profit websites and web based applications, MSC helps nonprofits communicate with their members and donors while maximizing online giving and engagement.</p>

  <div class="solutions">Solutions<br>Web Applications</div>

  <div class="ribbon" style="left:452px; top:475px; width:401px;"><span>Mobile Applications</span></div>
  <p class="copy" style="left:452px; top:513px; width:375px;">Meridian Systems Corporation implements mobile applications for phones and tablets to provide direct communications with members and donors enabling real-time, two way interaction.</p>

  <div class="ribbon" style="left:452px; top:607px; width:401px;"><span>Systems Integration</span></div>
  <p class="copy" style="left:452px; top:645px; width:375px;">Every nonprofit's IT applications are scattered and disconnected. Meridian Systems Corporation has decades of experience integrating these applications into a single cohesive system.</p>

  <div class="ribbon" style="left:452px; top:736px; width:401px;"><span>Business Intelligence and Reporting</span></div>
  <p class="copy" style="left:452px; top:775px; width:375px;">Meridian Systems Corporation can wrestle all of an organization's data into simple executive dashboards and reports.</p>

  <div class="ribbon" style="left:452px; top:840px; width:401px;"><span>Cloud Migration</span></div>
  <p class="copy" style="left:452px; top:881px; width:375px;">Reduce IT costs by migrating to the latest cloud solutions.</p>

  <div class="ribbon" style="left:452px; top:932px; width:401px;"><span>Member Donor Database</span></div>
  <p class="copy" style="left:452px; top:973px; width:375px; text-align:left;">Meridian Systems Corporation's GiveTrack Member / Donor CRM system is fully customized for each client meeting the unique needs of your organization</p>

  <footer class="footer-band"></footer>
</main>
</body>
</html>
```